Brovanek Data Yellow rose letterhead

I have a new logo for my company but in its current form it is too large to be used on letterhead or as a email signature. I need to have the designer use elements from the current logo and create something close to the original but more suited for smaller items.
Updates

I just uploaded a copy of our logo that does not have the weathered affect. Thanks

Reason: More time for revisions

Industry/Entity Type

It Company

Requirements
Must have
• The design must maintain the visual effect of the current logo. It needs to include the yellow rose and the name of the company.
Nice to have
• It would be nice to maintain the stamp theme and incorporate my name, address, phone, email. etc.

```html
<!DOCTYPE html>
<html lang="en">
<head>
<meta charset="utf-8">
<title>Brovanek Data Letterhead</title>
<link href="https://fonts.googleapis.com/css2?family=Baloo+2:wght@600;700&display=swap" rel="stylesheet">
<style>
  :root {
    --paper: #ffffff;
    --ink-brown: #5a3b2e;
    --rose-yellow: #ffc917;
    --rose-pale: #fdf2c6;
  }
  html, body {
    margin: 0;
    padding: 0;
    overflow: hidden;
    background: var(--paper);
  }
  .letterhead {
    position: relative;
    width: 927px;
    height: 1200px;
    background: var(--paper);
    overflow: hidden;
    font-family: "Baloo 2", sans-serif;
  }
  .brand {
    position: absolute;
    left: 26px;
    top: 33px;
    width: 175px;
    height: 150px;
    display: flex;
    flex-direction: column;
    align-items: center;
    justify-content: center;
    gap: 10px;
  }
  .brand-mark {
    width: 74px;
    height: 74px;
    border-radius: 50%;
    background: var(--rose-yellow);
  }
  .brand-name {
    margin: 0;
    font-size: 24px;
    font-weight: 700;
    line-height: 1;
    color: var(--ink-brown);
    white-space: nowrap;
  }
  .contact {
    position: absolute;
    left: 220px;
    top: 43px;
    margin: 0;
    padding: 0;
    list-style: none;
    font-size: 14.5px;
    font-weight: 600;
    line-height: 27.5px;
    color: var(--ink-brown);
  }
  .footer-band {
    position: absolute;
    left: 0;
    bottom: 0;
    width: 927px;
    height: 106px;
    background: linear-gradient(90deg,
      var(--rose-yellow) 0%,
      var(--rose-yellow) 14%,
      var(--rose-pale) 32%,
      var(--rose-pale) 66%,
      var(--rose-yellow) 86%,
      var(--rose-yellow) 100%);
  }
</style>
</head>
<body>
  <div class="letterhead">
    <div class="brand">
      <span class="brand-mark"></span>
      <p class="brand-name">Brovanek Data</p>
    </div>
    <ul class="contact">
      <li>Mara Quillen, PhD</li>
      <li>218 NW Cedar Ridge Rd, Ste 1450</li>
      <li>Pecan Hollow, TX 76501</li>
      <li>mara@brovanek-data.com</li>
      <li>1-800-555-0147</li>
    </ul>
    <div class="footer-band"></div>
  </div>
</body>
</html>
```